LEARN Business Skills so you can Earn a good living

size of the poster is 8”x 10.75" plus 0.25" bleed.
Please leave 1 inch on the bottoum for footer
I want a design a poster that will attract people's attention.
I appreciate a creative ad however the ad should not take away from being able to clearly read the text.
-I also appreciate a simple creative ad that is not too busy.
-you can use graphics, vectors, or pictures of real people.
-however, if you use real people it should be a white male that is wearing a white shirt and look like a professional person.

Target Market(s)

Potential young business people

Industry/Entity Type

education

Requirements
Must have
• easy to read the text
Nice to have
• I would like a "creative" simple ad that is easy to be read
Should not have
• pictures of women

```html
<!DOCTYPE html>
<html lang="en">
<head>
<meta charset="utf-8">
<title>Learn to Earn – Business Enrichment Course</title>
<link rel="stylesheet" href="https://fonts.googleapis.com/css2?family=Bebas+Neue&family=Poppins:wght@400;500;600;700;800&display=swap">
<style>
  :root {
    --navy-deep: #06112b;
    --navy: #0d2458;
    --navy-bright: #1c4fa0;
    --orange: #ff7a00;
    --white: #ffffff;
    --ink: #0b1633;
    --tag-line: #cfd6e4;
  }
  * { box-sizing: border-box; margin: 0; padding: 0; }
  html, body { width: 902px; height: 1200px; overflow: hidden; background: #e2e2e2; }
  .poster {
    position: relative;
    width: 902px; height: 1200px; overflow: hidden;
    background:
      radial-gradient(ellipse 420px 360px at 560px 260px, rgba(40,100,200,.45), transparent 70%),
      radial-gradient(ellipse 500px 300px at 300px 700px, rgba(30,80,170,.35), transparent 70%),
      linear-gradient(160deg, var(--navy) 0%, #0a1a42 45%, var(--navy-deep) 100%);
    font-family: "Poppins", sans-serif;
    color: var(--white);
  }
  .photo { position: absolute; }
  .photo--hero {
    left: 482px; top: 21px; width: 420px; height: 386px;
    background: radial-gradient(ellipse 160px 220px at 240px 230px, #e9ecf1 0%, #c9ced8 45%, rgba(20,40,80,0) 75%);
  }
  .photo--student {
    left: 21px; top: 948px; width: 320px; height: 252px;
    background: radial-gradient(ellipse 170px 150px at 150px 150px, #e6e9ef 0%, #b9c0cc 50%, rgba(20,40,80,0) 80%);
    z-index: 3;
  }
  .tagline-bar {
    position: absolute; left: 0; background: var(--orange);
    font-family: "Poppins", sans-serif; font-weight: 600; color: var(--white);
    line-height: 1; letter-spacing: 1px;
  }
  .tagline-bar--learn { top: 46px; width: 273px; height: 57px; font-size: 58px; padding: 3px 0 0 26px; }
  .tagline-bar--earn { top: 111px; width: 321px; height: 56px; font-size: 58px; padding: 2px 0 0 29px; }
  .headline {
    position: absolute; left: 25px;
    font-family: "Bebas Neue", sans-serif; line-height: .78; letter-spacing: -1px;
  }
  .headline--business { top: 193px; font-size: 120px; color: var(--white); }
  .headline--enrichment { top: 298px; font-size: 120px; color: var(--orange); }
  .headline--course { top: 407px; font-size: 120px; color: var(--white); }
  .promise {
    position: absolute; left: 312px; top: 408px; width: 590px; height: 85px;
    background: #f6f7fa; color: var(--ink);
    font-weight: 700; font-size: 20.5px; line-height: 1.3;
    padding: 13px 0 0 17px;
  }
  .skills-title {
    position: absolute; top: 570px; width: 100%; text-align: center;
    font-weight: 700; font-size: 27px; letter-spacing: .3px;
  }
  .skills-title span { color: var(--orange); }
  .benefit { position: absolute; top: 637px; display: flex; align-items: center; }
  .benefit__icon {
    width: 71px; height: 70px; background: var(--white); border-radius: 5px;
    box-shadow: 5px 5px 0 var(--orange);
    display: flex; align-items: center; justify-content: center;
  }
  .benefit__text { margin-left: 26px; font-size: 23px; line-height: 1.25; font-weight: 400; }
  .benefit--job { left: 28px; }
  .benefit--grow { left: 313px; }
  .benefit--grow .benefit__text { margin-left: 24px; }
  .benefit--salary { left: 624px; }
  .benefit--salary .benefit__text { margin-left: 33px; }
  .divider {
    position: absolute; left: 50px; top: 728px; width: 822px; height: 3px;
    background: linear-gradient(90deg, transparent, var(--orange) 15%, var(--orange) 85%, transparent);
  }
  .topics { position: absolute; left: 0; top: 760px; width: 100%; }
  .topics__row { display: flex; justify-content: center; gap: 10px; margin-bottom: 14px; }
  .topic {
    border: 2px solid var(--tag-line); border-radius: 4px;
    font-weight: 500; font-size: 14px; letter-spacing: .2px;
    height: 32px; line-height: 28px; padding: 0 8px; white-space: nowrap;
  }
  .register {
    position: absolute; left: 230px; top: 997px; display: flex; align-items: center; gap: 14px;
    font-weight: 700; font-size: 30px;
  }
  .footer {
    position: absolute; left: 160px; top: 1049px; width: 742px; height: 151px;
    background: var(--orange); border-top: 3px solid #e6e9ef; z-index: 2;
  }
  .footer__heading {
    position: absolute; left: 210px; top: 20px;
    font-family: "Bebas Neue", sans-serif; font-size: 40px; line-height: 1;
    color: var(--ink); border-bottom: 3px solid var(--ink); padding-bottom: 1px;
  }
  .footer__phone {
    position: absolute; left: 212px; top: 70px; display: flex; align-items: center; gap: 20px;
    font-family: "Bebas Neue", sans-serif; font-size: 56px; line-height: 1; color: var(--white);
  }
</style>
</head>
<body>
<main class="poster">
  <div class="photo photo--hero" role="img" aria-label="Smiling professional man in a white shirt holding an open laptop"></div>

  <div class="tagline-bar tagline-bar--learn">LEARN</div>
  <div class="tagline-bar tagline-bar--earn">TO EARN</div>

  <h1>
    <span class="headline headline--business">BUSINESS</span>
    <span class="headline headline--enrichment">ENRICHMENT</span>
    <span class="headline headline--course">COURSE</span>
  </h1>

  <p class="promise">A PROVEN SUCCESS OF HELPING PEOPLE<br>IN THEIR LIVELIHOODS</p>

  <h2 class="skills-title">BUSINESS SKILLS <span>THAT WILL HELP YOU</span></h2>

  <div class="benefit benefit--job">
    <div class="benefit__icon">
      <svg width="42" height="38" viewBox="0 0 42 38" aria-hidden="true">
        <rect x="3" y="10" width="36" height="25" rx="3" fill="#111"/>
        <rect x="14" y="4" width="14" height="8" rx="2" fill="none" stroke="#111" stroke-width="3"/>
        <rect x="3" y="19" width="36" height="2" fill="#fff"/>
        <rect x="18" y="17" width="6" height="6" fill="#fff" stroke="#111" stroke-width="1.5"/>
      </svg>
    </div>
    <p class="benefit__text">Get a<br>quality job</p>
  </div>

  <div class="benefit benefit--grow">
    <div class="benefit__icon">
      <svg width="46" height="42" viewBox="0 0 46 42" aria-hidden="true">
        <rect x="5" y="30" width="6" height="10" fill="#111"/>
        <rect x="15" y="24" width="6" height="16" fill="#111"/>
        <rect x="25" y="18" width="6" height="22" fill="#111"/>
        <rect x="35" y="12" width="6" height="28" fill="#111"/>
        <polyline points="3,24 15,16 24,19 40,4" fill="none" stroke="#111" stroke-width="3"/>
        <polygon points="42,1 42,11 33,3" fill="#111"/>
      </svg>
    </div>
    <p class="benefit__text">start/grow<br>your business</p>
  </div>

  <div class="benefit benefit--salary">
    <div class="benefit__icon">
      <svg width="46" height="44" viewBox="0 0 46 44" aria-hidden="true">
        <circle cx="26" cy="12" r="10" fill="#111"/>
        <text x="26" y="17" text-anchor="middle" font-family="Poppins, sans-serif" font-size="14" font-weight="700" fill="#fff">$</text>
        <rect x="3" y="26" width="6" height="16" fill="#111"/>
        <path d="M12 28 h14 a3 3 0 0 1 0 6 h-8 M12 40 h18 l12 -10" fill="none" stroke="#111" stroke-width="4" stroke-linejoin="round"/>
      </svg>
    </div>
    <p class="benefit__text">Increase<br>your salary</p>
  </div>

  <div class="divider"></div>

  <section class="topics" aria-label="Course topics">
    <div class="topics__row">
      <span class="topic">BUSINESS ADMINISTRATION</span>
      <span class="topic">SMALL BUSINESS MANAGEMENT</span>
      <span class="topic">FINANCE</span>
      <span class="topic">INVESTMENTS</span>
      <span class="topic">COMPUTERS</span>
    </div>
    <div class="topics__row">
      <span class="topic">ACCOUNTING</span>
      <span class="topic">SALES MARKETING</span>
      <span class="topic">PROJECT MANAGEMENT INTERVIEWING SKILLS</span>
      <span class="topic">BUSINESS LAW</span>
    </div>
    <div class="topics__row">
      <span class="topic">NEGOTIATION</span>
      <span class="topic">PUBLIC SPEAKING</span>
      <span class="topic">IMPORT/EXPORT</span>
      <span class="topic">INFORMATION TECHNOLOY</span>
      <span class="topic">DISTRIBUTION</span>
    </div>
    <div class="topics__row">
      <span class="topic">MARKETING</span>
      <span class="topic">LEDGERLY</span>
      <span class="topic">REAL ESTATE</span>
      <span class="topic">HEALTH CARE</span>
      <span class="topic">MANAGEMENT</span>
      <span class="topic">ORBITMART</span>
    </div>
  </section>

  <div class="photo photo--student" role="img" aria-label="Smiling man in glasses and a light shirt typing on a laptop"></div>

  <div class="register">
    <svg width="36" height="36" viewBox="0 0 36 36" aria-hidden="true">
      <rect x="3" y="5" width="22" height="28" rx="3" fill="none" stroke="#ff7a00" stroke-width="3"/>
      <rect x="9" y="2" width="10" height="6" rx="2" fill="#ff7a00"/>
      <line x1="8" y1="15" x2="20" y2="15" stroke="#ff7a00" stroke-width="3"/>
      <line x1="8" y1="22" x2="16" y2="22" stroke="#ff7a00" stroke-width="3"/>
      <circle cx="26" cy="26" r="9" fill="#ff7a00"/>
      <polyline points="21.5,26 25,29.5 30.5,22.5" fill="none" stroke="#fff" stroke-width="2.5"/>
    </svg>
    <span>GET REGISTERED NOW</span>
  </div>

  <footer class="footer">
    <p class="footer__heading">CONTACT US FOR MORE INFORMATION:</p>
    <p class="footer__phone">
      <svg width="36" height="36" viewBox="0 0 24 24" aria-hidden="true">
        <path fill="#0b1633" d="M6.6 10.8a15.1 15.1 0 0 0 6.6 6.6l2.2-2.2a1 1 0 0 1 1-.25 11.4 11.4 0 0 0 3.6.57 1 1 0 0 1 1 1V20a1 1 0 0 1-1 1A17 17 0 0 1 3 4a1 1 0 0 1 1-1h3.5a1 1 0 0 1 1 1c0 1.25.2 2.45.57 3.57a1 1 0 0 1-.25 1z"/>
      </svg>
      <span>555 0123 4567 89</span>
    </p>
  </footer>
</main>
</body>
</html>
```